Fun, Clean Business Card For Family Focused Travel Agency

I need a business card using specific colors and fonts as in the uploaded files. Ideally, I would like a large image of the logo on the back and all the contact info on the front. Maybe the stars/dots somewhere in a flowy form.

I do want it the contact information to be clear and easy to read. I don't want it to look too busy. Maybe even a bit minimalist.

I plan or ordering the ROUNDED CORNER business cards from Cardwell Press, so please consider that in your design.

Target Market(s)

Families with children, couples, groups of friends

Contact Information for Business Card

Marla Quint, Owner
Marla@TumbleTrips.example
Cell Phone Number 555-218-4603
Office Phone Number 555-647-1925
Specializing in Glimmerland destinations, Pelican Bay Fun Park, Cruises and All-Inclusive Vacations.

Nice but not required:
www.TumbleTrips.example
Facebook, Instagram, Twitter icons with username: TumbleTrips

Font styles to use
Sans Serif

Requirements
Must have
• Please try to use the colors from the logo as much as possible. I understand lighter shades/colors may be needed for some things.
Should not have
• NO SERIF FONTS. That is really the only thing I do not want at all

```html
<!DOCTYPE html>
<html lang="en">
<head>
<meta charset="utf-8">
<title>TumbleTrips – Business Card</title>
<link rel="stylesheet" href="https://fonts.googleapis.com/css2?family=Dancing+Script:wght@700&family=Fira+Sans:ital,wght@0,600;0,700;1,500&display=swap">
<style>
  :root {
    --backdrop: #d9f1ed;
    --paper: #ffffff;
    --teal: #13b39a;
    --navy: #001233;
    --orange: #ef7f00;
    --orange-fold: #b85a00;
    --gold: #f2b705;
    --ink-white: #ffffff;
  }
  * { margin: 0; padding: 0; box-sizing: border-box; }
  html, body {
    width: 1200px; height: 1200px; overflow: hidden;
    background: var(--backdrop);
    font-family: "Fira Sans", Arial, sans-serif;
  }
  .card {
    position: absolute;
    left: 286px;
    width: 630px; height: 408px;
    border-radius: 34px;
    overflow: hidden;
  }
  .card--front { top: 130px; background: var(--paper); }
  .card--back { top: 660px; background: var(--teal); }
  .card__shapes { position: absolute; inset: 0; }

  .holder {
    position: absolute;
    left: 150px; top: 172px;
    transform: translate(-50%, -50%) rotate(-52deg);
    text-align: center;
    white-space: nowrap;
  }
  .holder__name {
    display: block;
    font-family: "Dancing Script", cursive;
    font-weight: 700;
    font-size: 60px;
    line-height: 1;
    color: var(--navy);
  }
  .holder__title {
    display: block;
    margin-top: 2px;
    font-weight: 700;
    font-size: 24px;
    letter-spacing: 1px;
    color: var(--teal);
  }

  .contact {
    position: absolute;
    left: 312px; top: 148px;
    list-style: none;
  }
  .contact__item {
    display: flex; align-items: center;
    height: 27px;
    font-weight: 600;
    font-size: 18px;
    color: var(--ink-white);
  }
  .contact__icon { width: 20px; height: 20px; margin-right: 9px; flex: none; }

  .specialty {
    position: absolute;
    left: 326px; top: 257px;
    font-style: italic;
    font-weight: 500;
    font-size: 14.5px;
    line-height: 21px;
    color: var(--ink-white);
  }
  .specialty span { display: block; }
  .specialty span:nth-child(1) { padding-left: 10px; }
  .specialty span:nth-child(2) { padding-left: 5px; }

  .rule {
    position: absolute;
    left: 305px; top: 331px;
    width: 315px; height: 2px;
    background: var(--teal);
  }

  .social {
    position: absolute;
    left: 272px; top: 358px;
    display: flex; align-items: center;
  }
  .social__dot {
    width: 30px; height: 30px;
    border: 2px solid var(--gold);
    border-radius: 50%;
    margin-right: 10px;
  }
  .social__handle {
    font-weight: 600;
    font-size: 19px;
    color: var(--gold);
  }

  .brand {
    position: absolute;
    left: 0; right: 0; top: 0; bottom: 0;
    display: flex; align-items: center; justify-content: center;
    padding-bottom: 10px;
  }
  .brand__mark {
    width: 96px; height: 96px;
    border-radius: 50%;
    background: var(--ink-white);
    margin-right: 22px;
  }
  .brand__name {
    font-weight: 700;
    font-size: 60px;
    color: var(--ink-white);
  }
</style>
</head>
<body>

<section class="card card--front" aria-label="Business card front">
  <svg class="card__shapes" width="630" height="408" viewBox="0 0 630 408" aria-hidden="true">
    <polygon points="466,0 526,0 206,408 146,408" fill="var(--teal)"/>
    <polygon points="526,0 630,0 630,408 206,408" fill="var(--navy)"/>
    <polygon points="222,244 276,244 250,274" fill="var(--orange-fold)"/>
    <polygon points="306,132 630,132 630,244 222,244" fill="var(--orange)"/>
  </svg>

  <div class="holder">
    <span class="holder__name">Marla Quint</span>
    <span class="holder__title">OWNER</span>
  </div>

  <ul class="contact">
    <li class="contact__item">
      <svg class="contact__icon" viewBox="0 0 20 20" aria-hidden="true">
        <rect x="1" y="3" width="18" height="11" rx="1.5" fill="none" stroke="#fff" stroke-width="2"/>
        <rect x="7" y="15" width="6" height="2" fill="#fff"/>
      </svg>
      Marla@TumbleTrips.example
    </li>
    <li class="contact__item">
      <svg class="contact__icon" viewBox="0 0 20 20" aria-hidden="true">
        <rect x="5" y="1" width="10" height="18" rx="2" fill="none" stroke="#fff" stroke-width="2"/>
        <circle cx="10" cy="15.5" r="1" fill="#fff"/>
      </svg>
      555 - 218 - 4603
    </li>
    <li class="contact__item">
      <svg class="contact__icon" viewBox="0 0 20 20" aria-hidden="true">
        <rect x="1" y="1" width="18" height="18" rx="3" fill="#fff"/>
        <path d="M6 5c1-1 2 0 2.5 1.5S8 8 8 9s2 3 3 3 1.5-1 2.5-.5S15 13 14 14s-5 0-7-3-2-5-1-6z" fill="var(--orange)"/>
      </svg>
      555 - 647 - 1925
    </li>
  </ul>

  <p class="specialty">
    <span>Specializing in Glimmerland destinations,</span>
    <span>Pelican Bay Fun Park,</span>
    <span>Cruises and All-inclusive Vacations</span>
  </p>

  <div class="rule"></div>

  <div class="social">
    <span class="social__dot"></span>
    <span class="social__handle">TumbleTrips</span>
  </div>
</section>

<section class="card card--back" aria-label="Business card back">
  <div class="brand">
    <span class="brand__mark"></span>
    <span class="brand__name">TumbleTrips</span>
  </div>
</section>

</body>
</html>
```